WordPress Design (redesign) and Coding for Funeral Consulting Services & mobile app

I need an attractive SEO friendly WordPress design.

Incorporating all of the latest design standards in a graceful and appealing way. I'd like to see CTA's for for funeral consulting services. People should be able to purchase my consulting services directly from the website so I'd like to see nice buttons.

Funeral Consulting Services are the main topic for this website.

I also have an iOS app called Velomarque in the iOS Appvault Shelf. I want buttons and CTAs so that users can download the app right to their iOS device(s). Make this a secondary focus.

I want more of a mobile focus as that is where I expect the most traffic. Mobile users like to act quickly and they also like to scroll if their interest is captured so I want the design to reflect that.

End to end design
Large Creative Typography for increased mobile searchers.
attractive CTA’s
RGB Vivid / Bright Colors that match our logo
A menu that is easy to find and use on mobile devices
button(s) for iOS app download.

the current website is www.velomarque-example.com This website was a placeholder.
Updates

I'd need users to fill out a survey so that I may collect information from them to better provide service to them.

reference websites: Quillvant.com & Torbex.com for website design inspiratioin. reference Harnwick.com for blog

Target Market(s)

18-35 year old mobile users

Industry/Entity Type

Consulting

Coding

Coded - Design and coding required

Font styles to use
Sans Serif

Colors
fbee3d
000000
ffffff
cbcbcb
fefdec

Requirements
Must have
• iOS app logo and iOS app logo colors should have its own area/page
• CTA's for consulting services and app download. Main topic
• reviews (testimonials)
• Video area
• end to end design
• creative typography
Nice to have
• a beautiful blog page that blends well with the design
Should not have
• Any imagery related to funerals or burials.

```html
<!DOCTYPE html>
<html lang="en">
<head>
<meta charset="utf-8">
<title>Velomarque – Funeral Consulting Services</title>
<link rel="stylesheet" href="https://fonts.googleapis.com/css2?family=Great+Vibes&family=Montserrat:wght@400;600;700&family=Open+Sans:wght@400;600;700&display=swap">
<style>
:root{
  --yellow:#fbd21c;
  --yellow-soft:#fbee3d;
  --black:#000000;
  --ink:#1e1e1e;
  --text:#333333;
  --white:#ffffff;
  --grey:#cbcbcb;
  --panel:#ececec;
  --cream:#fefdec;
  --footer:#2a2a2a;
}
*{box-sizing:border-box;margin:0;padding:0}
html,body{width:1200px;height:4401px;overflow:hidden}
body{position:relative;background:var(--white);font-family:"Open Sans",Arial,sans-serif;color:var(--text)}
section,header,footer{position:absolute;left:0;width:1200px}
.abs{position:absolute}
.btn{position:absolute;display:flex;align-items:center;justify-content:center;height:52px;border-radius:26px;font-family:"Montserrat",Arial,sans-serif;font-weight:700;font-size:14px;letter-spacing:.3px;text-transform:uppercase}
.btn-dark{background:var(--black);color:var(--white)}
.btn-yellow{background:var(--yellow);color:var(--black)}
.section-title{position:absolute;left:0;width:1200px;text-align:center;font-family:"Montserrat",Arial,sans-serif;font-weight:700;font-size:28px;color:var(--black);letter-spacing:.5px}
.section-title span{color:var(--yellow)}
.section-title::after{content:"";display:block;width:96px;height:2px;background:var(--black);margin:18px auto 0}

/* header */
.site-header{top:0;height:118px;background:var(--white);border-bottom:1px solid #eee}
.brand{position:absolute;left:98px;top:36px;display:flex;align-items:center;gap:12px;font-family:"Montserrat",Arial,sans-serif;font-weight:700;font-size:32px;color:var(--black)}
.brand-dot{width:18px;height:18px;border-radius:50%;background:var(--yellow)}
.main-nav{position:absolute;left:440px;top:0;height:118px;display:flex}
.main-nav a{display:flex;align-items:center;padding:0 22px;height:118px;font-family:"Montserrat",Arial,sans-serif;font-size:15px;color:var(--ink);text-decoration:none}
.main-nav a.active{background:var(--yellow);color:var(--white)}

/* hero */
.hero{top:118px;height:815px;background:var(--yellow);overflow:hidden}
.hero-photo{position:absolute;left:0;top:0;width:1200px;height:540px;background:linear-gradient(160deg,#5b5b5b 0%,#3c3a38 45%,#6e6a66 75%,#2c2c2c 100%)}
.hero-photo::after{content:"";position:absolute;inset:0;background:rgba(0,0,0,.35)}
.hero-wave{position:absolute;left:0;top:380px}
.hero-title{position:absolute;left:0;top:106px;width:1200px;text-align:center;font-family:"Great Vibes",cursive;font-size:92px;color:var(--white)}
.hero-lead{position:absolute;left:210px;top:232px;width:780px;text-align:center;font-size:17px;line-height:26px;color:var(--white)}
.hero-badge{position:absolute;left:568px;top:457px;width:64px;height:64px;border-radius:50%;background:var(--yellow);border:5px solid var(--black)}
.hero-copy{position:absolute;left:115px;top:578px;width:970px;text-align:center;font-size:13.5px;line-height:24px;color:var(--ink)}

/* features */
.features{top:933px;height:719px}
.tile{position:absolute;width:600px;height:359px}
.tile-light{background:var(--white)}
.tile-photo{background:linear-gradient(135deg,#3a3a3a,#5a5550 55%,#262626)}
.tile p{position:absolute;font-size:17px;line-height:27px}
.tile-photo p{color:var(--white);font-size:15.5px;line-height:24px}
.tile-light p{color:var(--ink)}

/* testimonials */
.testimonials{top:1652px;height:631px;background:var(--panel)}
.quote-card{position:absolute;top:182px;width:400px;height:358px;background:var(--white);border:3px solid var(--yellow);border-radius:14px}
.quote-mark{position:absolute;font-family:Georgia,serif;font-size:90px;line-height:1;color:var(--yellow);font-weight:700}
.avatar{position:absolute;left:125px;top:32px;width:150px;height:150px;border-radius:50%;border:6px solid var(--yellow)}
.quote-text{position:absolute;left:30px;top:230px;width:340px;text-align:center;font-size:15px;line-height:24px;color:var(--text)}
.quote-name{position:absolute;left:0;top:312px;width:394px;text-align:center;font-size:15px;font-weight:600;color:var(--ink)}

/* video */
.video{top:2283px;height:528px;background:var(--white)}
.video-frame{position:absolute;left:170px;top:79px;width:860px;height:372px;border-radius:10px;overflow:hidden;background:linear-gradient(120deg,#cfc8c0 0%,#6e655c 40%,#2b2a2c 70%,#8a2b2b 100%)}
.play{position:absolute;left:560px;top:225px}

/* app */
.app{top:2811px;height:748px;background:var(--panel)}
.phone-card{position:absolute;top:152px;width:226px;height:455px;background:var(--yellow);overflow:hidden}
.phone-card p{position:absolute;left:14px;top:12px;width:198px;text-align:center;font-size:12.5px;line-height:18px;color:var(--white)}
.phone{position:absolute;left:16px;top:92px;width:194px;height:400px;border-radius:26px;background:var(--black)}
.phone-screen{position:absolute;left:10px;top:40px;width:174px;height:320px;background:linear-gradient(180deg,#f4f4f4,#dedede)}

/* blog */
.blog{top:3559px;height:480px;background:var(--white)}
.post{position:absolute;top:173px;width:460px;height:112px}
.post-thumb{position:absolute;left:0;top:0;width:152px;height:112px;border-radius:12px;background:linear-gradient(135deg,#c9c3bc,#4a4642 60%,#222)}
.post h3{position:absolute;left:167px;top:8px;font-family:"Montserrat",Arial,sans-serif;font-size:16px;font-weight:700;color:var(--ink)}
.post-date{position:absolute;left:167px;top:36px;display:flex;align-items:center;gap:8px;font-size:13px;color:var(--yellow);font-weight:600}
.post p{position:absolute;left:167px;top:60px;width:290px;font-size:13.5px;line-height:21px;color:#555;text-align:justify}

/* footer */
.site-footer{top:4000px;height:401px;background:var(--footer)}
.footer-curve{position:absolute;left:0;top:0}
.footer-brand{position:absolute;left:0;top:50px;width:1200px;display:flex;justify-content:center;align-items:center;gap:12px;font-family:"Montserrat",Arial,sans-serif;font-weight:700;font-size:34px;color:var(--white)}
.social{position:absolute;left:0;top:172px;width:1200px;display:flex;justify-content:center;gap:14px}
.social span{width:38px;height:38px;border-radius:50%;border:2px solid var(--white)}
.footer-nav{position:absolute;left:0;top:250px;width:1200px;display:flex;justify-content:center;font-family:"Montserrat",Arial,sans-serif;font-weight:600;font-size:14px;color:var(--white)}
.footer-nav a{color:var(--white);text-decoration:none;padding:0 20px;border-left:1px solid var(--white)}
.footer-nav a:first-child{border-left:none}
.footer-rule{position:absolute;left:100px;top:318px;width:1000px;height:1px;background:#666}
.copyright{position:absolute;left:0;top:355px;width:1200px;text-align:center;font-size:13px;font-weight:600;color:var(--white)}
</style>
</head>
<body>

<header class="site-header">
  <div class="brand"><span class="brand-dot"></span>Velomarque</div>
  <nav class="main-nav">
    <a class="active" href="#">HOME</a>
    <a href="#">ABOUT US</a>
    <a href="#">SERVICES</a>
    <a href="#">BLOG</a>
    <a href="#">TESTIMONIALS</a>
    <a href="#">CONTACT US</a>
  </nav>
</header>

<section class="hero">
  <div class="hero-photo" role="img" aria-label="Consultant meeting with clients in an office"></div>
  <svg class="hero-wave" width="1200" height="200" viewBox="0 0 1200 200" aria-hidden="true">
    <path d="M0 90 C 300 190, 700 200, 1200 40 L1200 200 L0 200 Z" fill="#fbd21c"/>
  </svg>
  <h1 class="hero-title">Funeral Consulting Services</h1>
  <p class="hero-lead">Funerals are expensive. Having to finance one suddenly can be &amp; burden to many families, especially those that are uninsured or unprepared.</p>
  <a class="btn btn-dark" style="left:502px;top:316px;width:196px;background:var(--yellow);color:var(--black)">Download Now</a>
  <div class="hero-badge"></div>
  <p class="hero-copy">Funerals are expensive. Having to finance one suddenly can be &amp; burden to manyfamilies, especially those that are uninsured or unprepared. Not coincidently, there is often &amp; windfall of money at this time, in the form of donations, family contributions, and life insurance proceeds. Families tend to consider that money ‘going away’ funds. The funeral industry wants to pressure you into spending your last dollar on that event.</p>
  <a class="btn btn-dark" style="left:455px;top:692px;width:290px">Don't Throw Money Away</a>
</section>

<section class="features">
  <div class="tile tile-light" style="left:0;top:0">
    <p style="left:40px;top:94px;width:520px;text-align:justify">The fact is, life insurance was never intended to be fully used on &amp; fancy funeral, but rather as &amp; hedge against disaster for the survivors.</p>
    <a class="btn btn-dark" style="left:40px;top:234px;width:170px">Save Money Now</a>
  </div>
  <div class="tile tile-photo" style="left:600px;top:0" role="img" aria-label="Consultant reviewing paperwork with a client">
    <p style="left:30px;top:58px;width:545px;font-size:17px;line-height:27px">A funeral consultant is someone who, on their own, goes out and does all the things related to making funeral arrangements. How ever we do so with your budget and your ideals in mind. We rep resent you as your spokes person and friend during this tough time.</p>
    <a class="btn btn-yellow" style="left:30px;top:245px;width:170px">Get Help ASAP</a>
  </div>
  <div class="tile tile-photo" style="left:0;top:359px" role="img" aria-label="Advisor talking with a couple at a desk">
    <p style="left:40px;top:42px;width:520px">The first step in funeral planning, particularly if you find yourself at-need, is to get &amp; friend by your side. This should be someone who is somewhat re moved from thedeceased, so the friend's emotions will not be &amp; factor. It should also be someone whose judgement you trust and, preferably, some one who has been through the arrangement process in the recent past.<br>This friend should be someone who h&amp;s the strength of character to say 'NO' or &amp;t least 'Not YET', to keep you from being pressured into hasty, expensive financi&amp;l decisions.</p>
    <a class="btn btn-yellow" style="left:40px;top:280px;width:180px">Save Money Today</a>
  </div>
  <div class="tile tile-light" style="left:600px;top:359px">
    <p style="left:35px;top:70px;width:530px">In &amp; survey of several thousand funeral directors, in response to the question Why would you say funerals cost so much?, over 85% replied "Emotional over spending by the family."</p>
    <a class="btn btn-dark" style="left:35px;top:231px;width:176px">Get Help Now</a>
  </div>
</section>

<section class="testimonials">
  <h2 class="section-title" style="top:78px">OUR <span>TESTIMONIALS</span></h2>
  <div class="quote-card" style="left:176px">
    <span class="quote-mark" style="left:28px;top:28px">“</span>
    <span class="quote-mark" style="left:312px;top:140px">”</span>
    <div class="avatar" role="img" aria-label="Portrait of customer Anna Smith" style="background:linear-gradient(160deg,#c7a58c,#7a5a48)"></div>
    <p class="quote-text">Sed ut perspiciatis unde omnis iste natus error sit voluptatem accusantium doloremque laudan tium, totam rem aperiam.</p>
    <p class="quote-name">- Anna Smith</p>
  </div>
  <div class="quote-card" style="left:627px">
    <span class="quote-mark" style="left:28px;top:28px">“</span>
    <span class="quote-mark" style="left:312px;top:140px">”</span>
    <div class="avatar" role="img" aria-label="Portrait of customer John Doe" style="background:linear-gradient(160deg,#b9a596,#5e4f45)"></div>
    <p class="quote-text">Sed ut perspiciatis unde omnis iste natus error sit voluptatem accusantium doloremque laudan tium, totam rem aperiam.</p>
    <p class="quote-name">- John Doe</p>
  </div>
</section>

<section class="video">
  <div class="video-frame" role="img" aria-label="Video still of a consultant taking notes with an elderly client"></div>
  <svg class="play" width="80" height="80" viewBox="0 0 80 80" aria-label="Play video">
    <circle cx="40" cy="40" r="34" fill="rgba(0,0,0,.25)" stroke="#fff" stroke-width="5"/>
    <path d="M32 24 L56 40 L32 56 Z" fill="#fff"/>
  </svg>
</section>

<section class="app">
  <h2 class="section-title" style="top:56px">DOWNLOAD <span>OUR APP</span></h2>
  <div class="phone-card" style="left:100px">
    <p>Keep your plans and notes in one place, ready when you need them.</p>
    <div class="phone"><div class="phone-screen" role="img" aria-label="App screen showing a user profile feed"></div></div>
  </div>
  <div class="phone-card" style="left:358px">
    <p>Share your wishes with family members and friends in a few simple taps.</p>
    <div class="phone"><div class="phone-screen" role="img" aria-label="App sign-in screen"></div></div>
  </div>
  <div class="phone-card" style="left:613px">
    <p>Compare costs and services side by side before you sign anything at all.</p>
    <div class="phone"><div class="phone-screen" role="img" aria-label="App screen with an image upload form"></div></div>
  </div>
  <div class="phone-card" style="left:871px">
    <p>Find trusted guidance and support near you, any hour of any day.</p>
    <div class="phone"><div class="phone-screen" role="img" aria-label="App welcome screen with a green landscape" style="background:linear-gradient(180deg,#cfe3ef,#8db36a 60%,#5d8a3c)"></div></div>
  </div>
  <a class="btn btn-dark" style="left:496px;top:634px;width:208px">Download App Now</a>
</section>

<section class="blog">
  <h2 class="section-title" style="top:62px">OUR <span>BLOG POSTS</span></h2>
  <article class="post" style="left:100px">
    <div class="post-thumb" role="img" aria-label="Businesswoman at a desk"></div>
    <h3>NEMO ENIM IPSAM</h3>
    <div class="post-date"><svg width="14" height="14" viewBox="0 0 14 14" aria-hidden="true"><rect x="1" y="2" width="12" height="11" rx="1.5" fill="none" stroke="#fbd21c" stroke-width="1.6"/><path d="M1 5.5h12" stroke="#fbd21c" stroke-width="1.6"/></svg>Nov 12</div>
    <p>Sed ut perspiciatis unde omnis iste natus error sit voluptatem accusantium.</p>
  </article>
  <article class="post" style="left:643px">
    <div class="post-thumb" role="img" aria-label="Two colleagues in a meeting"></div>
    <h3>NEMO ENIM IPSAM</h3>
    <div class="post-date"><svg width="14" height="14" viewBox="0 0 14 14" aria-hidden="true"><rect x="1" y="2" width="12" height="11" rx="1.5" fill="none" stroke="#fbd21c" stroke-width="1.6"/><path d="M1 5.5h12" stroke="#fbd21c" stroke-width="1.6"/></svg>Nov 12</div>
    <p>Sed ut perspiciatis unde omnis iste natus error sit voluptatem accusantium.</p>
  </article>
</section>

<footer class="site-footer">
  <svg class="footer-curve" width="1200" height="60" viewBox="0 0 1200 60" aria-hidden="true">
    <path d="M0 0 H1200 V10 C 900 60, 300 60, 0 10 Z" fill="#ffffff"/>
  </svg>
  <div class="footer-brand"><span class="brand-dot"></span>Velomarque</div>
  <div class="social"><span></span><span></span><span></span><span></span><span></span></div>
  <nav class="footer-nav">
    <a href="#">HOME</a><a href="#">OUR SERVICES</a><a href="#">ABOUT US</a><a href="#">BLOG</a><a href="#">TESTIMONIALS</a><a href="#">CONTACT US</a>
  </nav>
  <div class="footer-rule"></div>
  <p class="copyright">Copyrights © 2017 Velomarque. All Rights Reserved</p>
</footer>

</body>
</html>
```